RK Donnelly & Associates

Create a website encompassing design work already carried out for business card.
Small accounting practice, business accounting and management, superannuation, audit, taxation.

```html
<!DOCTYPE html>
<html lang="en">
<head>
<meta charset="utf-8">
<title>RK Donnelly &amp; Associates</title>
<link href="https://fonts.googleapis.com/css2?family=Nunito:wght@400;600;700&display=swap" rel="stylesheet">
<style>
:root{
  --ink-dark:#1f2022;
  --nav-dark:#2b2c2e;
  --accent:#6ea6da;
  --heading:#4b87c1;
  --page:#fbfbfb;
  --panel:#f2f2f2;
  --panel-line:#e2e2e2;
  --body-text:#8a8a8a;
  --strong-text:#3b3b3b;
  --white:#ffffff;
}
*{margin:0;padding:0;box-sizing:border-box}
html,body{width:859px;height:1200px;overflow:hidden}
body{background:var(--page);font-family:"Nunito",sans-serif;color:var(--body-text);position:relative}
.abs{position:absolute}
.site-header{left:0;top:0;width:859px;height:70px;background:var(--ink-dark)}
.brand{left:52px;top:20px;display:flex;align-items:center;gap:9px}
.brand-mark{width:28px;height:28px;background:var(--accent)}
.brand-name{font-family:"Nunito",sans-serif;font-weight:600;color:var(--white);font-size:14px;white-space:nowrap}
.call{right:53px;top:33px;color:#d8d8d8;font-size:15px}
.call span{color:var(--accent)}
.tagline{left:0;top:70px;width:859px;height:18px;background:var(--accent);color:var(--white);font-size:5.5px;font-weight:700;padding:5px 0 0 61px}
.main-nav{left:0;top:88px;width:859px;height:30px;background:linear-gradient(#3a3b3d,#242527);display:flex;align-items:center;padding-left:65px}
.main-nav a{color:#e6e6e6;text-decoration:none;font-size:9px;text-transform:uppercase}
.hero{left:53px;top:120px;width:753px;height:272px;background:linear-gradient(100deg,#c9d4de 0%,#7f98ad 35%,#5b6670 60%,#9aa4ad 100%)}
.hero-caption{left:436px;top:206px;width:370px;height:100px;background:rgba(245,245,245,.88);padding:10px 24px}
.hero-caption h2{color:var(--heading);font-weight:600;font-size:18px;letter-spacing:.3px}
.hero-caption p{color:#444;font-size:11.5px;line-height:18px;margin-top:4px}
.dots{left:405px;top:372px;display:flex;gap:5px}
.dots i{width:9px;height:9px;border-radius:50%;background:var(--white)}
.dots i:first-child{background:var(--accent)}
h3.section-title{color:var(--heading);font-weight:400;font-size:17px;text-transform:uppercase;letter-spacing:.2px}
.copy{font-size:7.5px;line-height:16.5px}
.btn{background:#353638;color:#eee;font-size:8.5px;text-transform:uppercase;display:flex;align-items:center;justify-content:center}
.welcome-img{left:53px;top:422px;width:236px;height:165px;background:linear-gradient(135deg,#d6dde6,#7d92ad 60%,#4e6585)}
.welcome{left:311px;top:418px;width:495px}
.welcome .copy{margin-top:5px}
.welcome .btn{width:99px;height:28px;margin-top:12px}
.rule{left:53px;top:606px;width:753px;height:1px;background:#e3e3e3}
.panel{background:var(--panel);border:1px solid var(--panel-line)}
.services{left:53px;top:627px;width:236px;height:371px;padding:10px 13px}
.services-img{width:208px;height:108px;margin-top:6px;background:linear-gradient(120deg,#eef1f4,#9aa8b8 50%,#3d4654)}
.services .copy{font-size:7.5px;line-height:15px;margin-top:6px}
.service-list{list-style:none;margin-top:6px}
.service-list li{color:var(--heading);font-size:8.5px;height:24px;display:flex;align-items:center;gap:6px}
.service-list svg{width:8px;height:8px}
.services .btn{width:85px;height:22px;margin-top:7px}
.news{left:311px;top:627px;width:495px;height:173px;padding:10px 15px}
.news-item{display:flex;gap:13px;margin-top:8px}
.news-thumb{width:66px;height:52px;flex:none;background:linear-gradient(135deg,#e7e9ec,#8b95a1 60%,#3f4652)}
.news-date{color:var(--strong-text);font-size:9.5px;font-weight:600}
.news-item .copy{font-size:7.2px;line-height:13.5px}
.team{left:311px;top:822px;width:495px;height:174px;padding:10px 15px}
.team-row{display:flex;gap:12px;margin-top:8px}
.team-photo{width:108px;height:116px;background:linear-gradient(#e6e6e6,#b9b3ad)}
.clients-title{left:52px;top:1016px}
.blog-title{left:590px;top:1016px}
.pager{display:flex;gap:6px}
.pager svg{width:6px;height:9px}
.client-pager{left:529px;top:1025px}
.blog-pager{left:789px;top:1025px}
.client-logos{left:52px;top:1050px;display:flex;gap:8px}
.client{width:118px;height:54px;background:var(--white);border:1px solid #e6e6e6;display:flex;align-items:center;justify-content:center;gap:6px;color:#333;font-size:13px;font-weight:600;white-space:nowrap}
.client i{width:10px;height:10px;border-radius:50%;background:#e8742b}
.blog{left:590px;top:1047px;width:216px}
.blog .copy{font-size:7.2px;line-height:13.5px;margin-top:3px}
.site-footer{left:0;top:1118px;width:859px;height:82px;background:var(--nav-dark)}
.footer-brand{left:52px;top:1134px;display:flex;align-items:center;gap:8px}
.footer-brand .brand-mark{width:24px;height:24px}
.footer-brand .brand-name{font-size:12px}
.copyright{left:52px;top:1178px;font-size:7px;color:#8d8d8d}
.social{left:730px;top:1152px;display:flex;gap:8px}
.social i{width:20px;height:20px;border-radius:50%;display:block}
</style>
</head>
<body>
<header class="site-header abs">
  <div class="brand abs"><span class="brand-mark"></span><span class="brand-name">RK Donnelly &amp; Associates</span></div>
  <div class="call abs">Call Us: <span>123-555-0142</span></div>
</header>
<div class="tagline abs">Accountant · Business Solutions · Management · Superannuation · Audit</div>
<nav class="main-nav abs">
  <a style="margin-right:40px">Home</a><a style="margin-right:37px">About Us</a><a style="margin-right:37px">Our Services</a><a style="margin-right:37px">Latest News</a><a style="margin-right:37px">Our Team</a><a style="margin-right:37px">Blog</a><a style="margin-right:37px">Clients</a><a style="margin-right:37px">Careers</a><a>Contact Us</a>
</nav>

<div class="hero abs" role="img" aria-label="Photo of a smiling businessman in front of colleagues meeting in an office by the harbour"></div>
<div class="hero-caption abs">
  <h2>LOREM IPSUM DOLOR SIT AMET</h2>
  <p>Vivamus egestas risus in magna varius commodo. Sed semper viverra egestas. Etiam pretium porttitor lectus, vel ornare neque porta volutpat.</p>
</div>
<div class="dots abs"><i></i><i></i><i></i><i></i></div>

<div class="welcome-img abs" role="img" aria-label="Photo of a hand touching a rising growth chart"></div>
<section class="welcome abs">
  <h3 class="section-title">Welcome to our website</h3>
  <p class="copy">Aliquam molestie, mi et imperdiet euismod, dui purus auctor tellus, et interdum lacus lectus et ante. Sed accumsan sollicitudin sapien, sit amet adipiscing turpis gravida ac. In congue, neque ac lobortis volutpat, libero mauris varius mi, vitae suscipit ipsum ligula vitae risus. Duis aliquam nibh a dui iaculis viverra id a velit. Vivamus egestas risus in magna varius commodo. Sed semper viverra egestas. Etiam pretium porttitor lectus, vel ornare neque porta volutpat. Ut et scelerisque ante. Donec erat purus, faucibus vitae congue vel, porttitor nec lectus. Aenean a nibh eget turpis vehicula tempus ac sed massa..</p>
  <div class="btn">Read more ››</div>
</section>

<div class="rule abs"></div>

<section class="services panel abs">
  <h3 class="section-title">Our services</h3>
  <div class="services-img" role="img" aria-label="Photo of a business team reviewing documents at a table"></div>
  <p class="copy">Aliquam molestie, mi et imperdiet euismod, dui purus auctor tellus, et interdum lacus lectus et ante.</p>
  <ul class="service-list">
    <li><svg viewBox="0 0 8 8"><path d="M1 4.2 3 6.2 7 1.5" fill="none" stroke="#333" stroke-width="1.4"/></svg>Small Accounting Practice</li>
    <li><svg viewBox="0 0 8 8"><path d="M1 4.2 3 6.2 7 1.5" fill="none" stroke="#333" stroke-width="1.4"/></svg>Business Accounting and Management</li>
    <li><svg viewBox="0 0 8 8"><path d="M1 4.2 3 6.2 7 1.5" fill="none" stroke="#333" stroke-width="1.4"/></svg>Superannuation</li>
    <li><svg viewBox="0 0 8 8"><path d="M1 4.2 3 6.2 7 1.5" fill="none" stroke="#333" stroke-width="1.4"/></svg>Audit</li>
    <li><svg viewBox="0 0 8 8"><path d="M1 4.2 3 6.2 7 1.5" fill="none" stroke="#333" stroke-width="1.4"/></svg>Taxation</li>
  </ul>
  <div class="btn">Read more</div>
</section>

<section class="news panel abs">
  <h3 class="section-title">Latest news</h3>
  <div class="news-item">
    <div class="news-thumb" role="img" aria-label="Photo of financial papers on a desk"></div>
    <div><div class="news-date">Sep12, 2014</div><p class="copy">Aliquam molestie, mi et imperdiet euismod, dui purus auctor tellus, et interdum lacus lectus et ante. Sed accumsan sollicitudin sapien, sit amet adipiscing turpis gravida ac. In congue, neque ac lobortis volutpat..</p></div>
  </div>
  <div class="news-item">
    <div class="news-thumb" role="img" aria-label="Photo of hands reviewing a report"></div>
    <div><div class="news-date">Sep12, 2014</div><p class="copy">Aliquam molestie, mi et imperdiet euismod, dui purus auctor tellus, et interdum lacus lectus et ante. Sed accumsan sollicitudin sapien, sit amet adipiscing turpis gravida ac. In congue, neque ac lobortis volutpat..</p></div>
  </div>
</section>

<section class="team panel abs">
  <h3 class="section-title">Our team</h3>
  <div class="team-row">
    <div class="team-photo" role="img" aria-label="Portrait of a team member"></div>
    <div class="team-photo" role="img" aria-label="Portrait of a team member"></div>
    <div class="team-photo" role="img" aria-label="Portrait of a team member"></div>
    <div class="team-photo" role="img" aria-label="Portrait of a team member"></div>
  </div>
</section>

<h3 class="section-title clients-title abs">Our client</h3>
<div class="pager client-pager abs"><svg viewBox="0 0 6 9"><path d="M5 1 1.5 4.5 5 8" fill="none" stroke="#4b87c1" stroke-width="1.2"/></svg><svg viewBox="0 0 6 9"><path d="M1 1 4.5 4.5 1 8" fill="none" stroke="#4b87c1" stroke-width="1.2"/></svg></div>
<div class="client-logos abs">
  <div class="client"><i></i>Corvelle</div>
  <div class="client">Ambrith Co</div>
  <div class="client"><i></i>Pellamor</div>
  <div class="client"><i></i>Quintaro</div>
</div>

<h3 class="section-title blog-title abs">Blog</h3>
<div class="pager blog-pager abs"><svg viewBox="0 0 6 9"><path d="M5 1 1.5 4.5 5 8" fill="none" stroke="#4b87c1" stroke-width="1.2"/></svg><svg viewBox="0 0 6 9"><path d="M1 1 4.5 4.5 1 8" fill="none" stroke="#4b87c1" stroke-width="1.2"/></svg></div>
<section class="blog abs">
  <div class="news-date">Sep12, 2014</div>
  <p class="copy">Aliquam molestie, mi et imperdiet euismod, dui purus auctor tellus, et interdum lacus lectus et ante. Sed accumsan sollicitudin sapien, sit...</p>
</section>

<footer class="site-footer abs"></footer>
<div class="footer-brand abs"><span class="brand-mark"></span><span class="brand-name">RK Donnelly &amp; Associates</span></div>
<div class="copyright abs">Copyright © 2014. All Right Reserved . Privacy Policy</div>
<div class="social abs">
  <i style="background:#3b6fb3" aria-label="Social link"></i>
  <i style="background:#35a3dd" aria-label="Social link"></i>
  <i style="background:#e48a2a" aria-label="Feed link"></i>
</div>
</body>
</html>
```